Building Design company needing a letterhead

We need a letter head for our Building Design company to send letters etc. to our clients, consultants, councils etc. We would like to see our logo used and company colours. I have attached our style guide and an example of our current letterheads. Top left we would like our logo, top right we would like the company details and at the footer we would like some sort of image/design etc. that suits our brand. I like the Tarrow Design letterhead attached.

Target Market(s)

Professionals, Councils, Consultants, Mums & Dads

Industry/Entity Type

Architecture

Other font styles liked:
• refer the design style guide

Colors
f37122
000000
1b1b1b

Requirements
Must have
• Must have the minimum of a logo, company details and footer
Nice to have
• An image/design made for the footer that would suite our brand and website at www.corvanplans.com.au. Also it would be nice to include the KMEOT logo somewhere perhaps included in the footer.
Should not have
• Large images in the header. I just want the logo and company details.

```html
<!DOCTYPE html>
<html lang="en">
<head>
<meta charset="utf-8">
<title>Corvan Design Letterhead</title>
<link href="https://fonts.googleapis.com/css2?family=Arimo:wght@400;700&display=swap" rel="stylesheet">
<style>
  :root {
    --brand-orange: #ee7b43;
    --ink-black: #1e1816;
    --text-grey: #3a3a3a;
    --rule-gold: #e2b77a;
    --paper: #ffffff;
  }
  html, body {
    margin: 0;
    padding: 0;
    overflow: hidden;
    background: var(--paper);
  }
  .letterhead {
    position: relative;
    width: 967px;
    height: 1200px;
    background: var(--paper);
    font-family: "Arimo", Arial, sans-serif;
    overflow: hidden;
  }
  .letterhead__brand {
    position: absolute;
    left: 36px;
    top: 48px;
    display: flex;
    align-items: center;
    gap: 16px;
  }
  .brand-square {
    width: 40px;
    height: 40px;
    background: var(--brand-orange);
  }
  .brand-name {
    font-size: 34px;
    font-weight: 700;
    letter-spacing: 1px;
    color: var(--ink-black);
    line-height: 1;
  }
  .letterhead__details {
    position: absolute;
    right: 38px;
    top: 28px;
    text-align: right;
  }
  .details-key {
    margin: 0;
    font-size: 14px;
    font-weight: 700;
    letter-spacing: 0.4px;
    color: var(--brand-orange);
    line-height: 21px;
  }
  .details-address {
    margin: 6px 0 0;
    font-size: 14px;
    font-weight: 400;
    letter-spacing: 0.3px;
    color: var(--text-grey);
    line-height: 21px;
    font-style: normal;
  }
  .letterhead__rule {
    position: absolute;
    left: 0;
    top: 133px;
    width: 100%;
    height: 1px;
    background: var(--rule-gold);
  }
  .letterhead__footer {
    position: absolute;
    left: 0;
    top: 1119px;
    width: 967px;
    height: 54px;
  }
  .footer-bands {
    position: absolute;
    left: 0;
    top: 0;
  }
  .footer-email,
  .footer-web {
    position: absolute;
    font-size: 17px;
    font-weight: 700;
    color: var(--paper);
    line-height: 1;
  }
  .footer-email { left: 56px; top: 15px; }
  .footer-web { right: 44px; top: 22px; }
</style>
</head>
<body>
  <main class="letterhead">
    <header>
      <div class="letterhead__brand">
        <span class="brand-square" aria-hidden="true"></span>
        <span class="brand-name">CORVAN DESIGN</span>
      </div>
      <div class="letterhead__details">
        <p class="details-key">PHONE (08) 5550 2714</p>
        <p class="details-key">ABN 41 208 317 964</p>
        <address class="details-address">
          Unit 2/8 Harlow Way Brackton WA 6100<br>
          PO Box 3150 Brackton North WA 6100
        </address>
      </div>
    </header>
    <div class="letterhead__rule"></div>

    <footer class="letterhead__footer">
      <svg class="footer-bands" width="967" height="54" viewBox="0 0 967 54" aria-hidden="true">
        <polygon points="444,54 475,8 967,8 967,54" fill="var(--brand-orange)"/>
        <polygon points="0,0 506,0 475,46 0,46" fill="var(--ink-black)"/>
      </svg>
      <span class="footer-email">admin@corvanplans.com.au</span>
      <span class="footer-web">www.corvanplans.com.au</span>
    </footer>
  </main>
</body>
</html>
```